Wine Bottle Label Logo Design

My fiancé and I are getting married in September and we made homemade wine which will be given to the guests as a wedding favor. We need label/logo for our wine bottles. We were looking for something rustic yet modern and simple. We had an idea for beige and cranberry colored wine stained, weathered, imperfect heart. Things that will need to be incorporated into the label design are as follows:
Our last name and also the name of the wine: Carudi
The year: 2012
Where is says Alcohol Content on a wine bottle normally write: Alcohol: Deceiving% by vol.
Type of wine: Red Wine
Incorporate our wedding date: Foot Stomped and Bottled for Marla and Ned's Wedding Day 9/28/13

```html
<!DOCTYPE html>
<html lang="en">
<head>
<meta charset="utf-8">
<title>Carudi Wine Labels</title>
<link rel="stylesheet" href="https://fonts.googleapis.com/css2?family=Nothing+You+Could+Do&display=swap">
<style>
  :root {
    --backdrop: #efeeec;
    --label: #ffffff;
    --stain: #8c615a;
    --stain-soft: #a87f72;
    --ribbon: #b48c7a;
    --ink: #3a2f2c;
    --ink-light: #fbf6f2;
  }
  * { margin: 0; padding: 0; box-sizing: border-box; }
  html, body {
    width: 1085px;
    height: 1200px;
    overflow: hidden;
    background: var(--backdrop);
  }
  .canvas {
    position: relative;
    width: 1085px;
    height: 1200px;
    font-family: "Nothing You Could Do", cursive;
    color: var(--ink);
  }
  .label {
    position: absolute;
    top: 360px;
    background: var(--label);
    box-shadow: 0 2px 10px rgba(0,0,0,0.08);
    display: flex;
    flex-direction: column;
    align-items: center;
    text-align: center;
  }
  .label--front { left: 170px; width: 335px; height: 480px; padding-top: 46px; }
  .label--back { left: 590px; width: 328px; height: 474px; padding: 32px 22px 0; }

  .brand-dot {
    border-radius: 50%;
    background: radial-gradient(circle at 40% 35%, var(--stain-soft), var(--stain) 70%);
  }
  .label--front .brand-dot { width: 190px; height: 190px; }
  .label--back .brand-dot { width: 64px; height: 64px; }

  .brand-name { color: var(--stain); line-height: 1; font-weight: 400; }
  .label--front .brand-name { font-size: 60px; margin-top: 22px; }
  .label--back .brand-name { font-size: 24px; margin-top: 8px; }

  .ribbon {
    position: relative;
    margin-top: 34px;
    width: 290px;
    height: 62px;
  }
  .ribbon svg { position: absolute; inset: 0; }
  .ribbon-text {
    position: absolute;
    left: 26px; right: 26px; top: 13px;
    font-size: 9.5px;
    line-height: 1.35;
    white-space: nowrap;
    color: var(--ink-light);
  }

  .vintage { font-size: 24px; margin-top: 8px; letter-spacing: 2px; }
  .varietal { font-size: 12px; margin-top: 8px; }
  .tasting-note { font-size: 14px; line-height: 2.1; margin-top: 4px; }
  .alcohol { font-size: 12px; margin-top: auto; margin-bottom: 30px; }
</style>
</head>
<body>
<main class="canvas">

  <section class="label label--front">
    <div class="brand-dot" aria-hidden="true"></div>
    <h1 class="brand-name">Carudi</h1>
    <div class="ribbon">
      <svg width="290" height="62" viewBox="0 0 290 62" aria-hidden="true">
        <path d="M0 22 L34 18 L28 38 L34 56 L0 52 L12 37 Z" fill="var(--stain-soft)"/>
        <path d="M290 22 L256 18 L262 38 L256 56 L290 52 L278 37 Z" fill="var(--stain-soft)"/>
        <path d="M26 10 Q145 -2 264 10 L264 46 Q145 34 26 46 Z" fill="var(--ribbon)"/>
      </svg>
      <p class="ribbon-text">Foot Stomped and Bottled for Marla and Ned's<br>Wedding Day 9/28/13</p>
    </div>
  </section>

  <section class="label label--back">
    <div class="brand-dot" aria-hidden="true"></div>
    <p class="brand-name">Carudi</p>
    <p class="vintage">2012</p>
    <p class="varietal">Red Wine</p>
    <p class="tasting-note">Aged outdoors during the cold<br>winter months to allow for a slower<br>fermentation process. Its like a<br>warm sweet hug in a bottle.</p>
    <p class="alcohol">Alcohol: Deceiving% by vol.</p>
  </section>

</main>
</body>
</html>
```